New Business Card Design Project

We require a business card design for Vexalund, a newly established Indian company.
Our focus is on the development, manufacturing, and export of a diverse array of pharmaceutical products on a global scale. The card should convey a professional appearance, as our primary markets are in Africa, China, and Southeast Asian nations.
We envision a two-sided business card, with the reverse side dedicated to a logo set against a solid color or an elegantly designed pattern. The corners should be rounded. We would appreciate seeing both horizontal and vertical design options. We trust the designer to utilize their expertise in creating this design.

The content for the business card is included in the attached Word file.

Target Market(s)

Our primary markets are in Africa, China, and Southeast Asian, Latin America, Maldives, Sri Lanka

Industry/Entity Type

Pharmaceutical Manufacturing and Export

Contact Information for Business Card

Colors

Designer to choose colors to be used in the design.

Requirements
Must have
• The reverse side of the business card features solely the logo along with the tagline, "Remedies of Life."
Should not have
• The logo should not exceed two instances, encompassing both the front and back sides of the card.

```html
<!DOCTYPE html>
<html lang="en">
<head>
<meta charset="utf-8">
<title>Vexalund Business Card</title>
<link href="https://fonts.googleapis.com/css2?family=Poppins:wght@400;500;700&display=swap" rel="stylesheet">
<style>
  :root {
    --backdrop: #2a2a2a;
    --card: #ffffff;
    --brand-blue: #29a8e0;
    --brand-red: #f0604d;
    --ink: #2b2b2b;
  }
  * { margin: 0; padding: 0; box-sizing: border-box; }
  html, body {
    width: 1200px; height: 900px; overflow: hidden;
    background: var(--backdrop);
    font-family: "Poppins", sans-serif;
  }
  .card {
    position: absolute;
    left: 290px;
    width: 620px; height: 354px;
    background: var(--card);
    border-radius: 18px;
    overflow: hidden;
    box-shadow: 0 10px 30px rgba(0,0,0,0.45);
  }
  .card--front { top: 60px; }
  .card--back { top: 476px; }

  .wordmark {
    display: flex; align-items: center; gap: 14px;
    color: var(--brand-blue);
    font-weight: 700;
    letter-spacing: 0.5px;
  }
  .wordmark__dot {
    border-radius: 50%;
    background: var(--brand-red);
    flex: none;
  }
  .card--front .wordmark {
    position: absolute; left: 50%; top: 50%;
    transform: translate(-50%, -50%);
    font-size: 74px;
  }
  .card--front .wordmark__dot { width: 34px; height: 34px; }

  .card--back .wordmark {
    position: absolute; left: 44px; top: 132px;
    font-size: 40px;
  }
  .card--back .wordmark__dot { width: 22px; height: 22px; }

  .divider {
    position: absolute; left: 318px; top: 62px;
    width: 1px; height: 196px;
    background: var(--brand-blue);
  }
  .contact {
    position: absolute; left: 342px; top: 52px;
    color: var(--ink);
  }
  .contact__name {
    color: var(--brand-blue);
    font-weight: 700; font-size: 24px; line-height: 1.1;
  }
  .contact__role { font-size: 13px; line-height: 1.35; margin-top: 4px; }
  .contact__address { font-size: 13px; line-height: 1.35; margin-top: 12px; }
  .contact__list { list-style: none; margin-top: 12px; }
  .contact__item {
    display: flex; align-items: center; gap: 9px;
    font-size: 13px; line-height: 1.55;
  }
  .contact__icon { width: 13px; height: 13px; flex: none; }

  .bands { position: absolute; left: 0; bottom: 0; width: 620px; height: 60px; }
</style>
</head>
<body>

<section class="card card--front" aria-label="Card front">
  <div class="wordmark">
    <span class="wordmark__dot"></span>
    <span class="wordmark__name">Vexalund</span>
  </div>
</section>

<section class="card card--back" aria-label="Card back">
  <div class="wordmark">
    <span class="wordmark__dot"></span>
    <span class="wordmark__name">Vexalund</span>
  </div>

  <div class="divider"></div>

  <div class="contact">
    <p class="contact__name">Rohan K. Talwade</p>
    <p class="contact__role">CEO<br>Vexalund</p>
    <p class="contact__address">14, Nilkamal Colony, 440712<br>Sarvapur, India</p>
    <ul class="contact__list">
      <li class="contact__item">
        <svg class="contact__icon" viewBox="0 0 16 16" aria-hidden="true">
          <path fill="#f0604d" d="M3 2h3l1.5 3.5-2 1.2a8 8 0 0 0 3.8 3.8l1.2-2L14 10v3a1 1 0 0 1-1 1A11 11 0 0 1 2 3a1 1 0 0 1 1-1z"/>
        </svg>
        +919800012345
      </li>
      <li class="contact__item">
        <svg class="contact__icon" viewBox="0 0 16 16" aria-hidden="true">
          <rect x="1" y="3" width="14" height="10" rx="1.5" fill="#f0604d"/>
          <path d="M2 4.5 8 9l6-4.5" fill="none" stroke="#fff" stroke-width="1.3"/>
        </svg>
        rtalwade@vexalund.com
      </li>
      <li class="contact__item">
        <svg class="contact__icon" viewBox="0 0 16 16" aria-hidden="true">
          <circle cx="8" cy="8" r="7" fill="#f0604d"/>
          <path d="M1 8h14M8 1c-3 3-3 11 0 14M8 1c3 3 3 11 0 14" fill="none" stroke="#fff" stroke-width="1"/>
        </svg>
        www.vexalund.com
      </li>
    </ul>
  </div>

  <svg class="bands" viewBox="0 0 620 60" preserveAspectRatio="none" aria-hidden="true">
    <polygon points="0,52 420,28 404,60 0,60" fill="#29a8e0"/>
    <polygon points="432,27 620,16 620,60 414,60" fill="#f0604d"/>
  </svg>
</section>

</body>
</html>
```